Design website for new email startup

We are starting a company called Pingo.QZ (it will live at http://pingo.qz).

We would like the main landing page for our site designed. We have provided a very simple wireframe to help provide direction for the content it should include, but we do not expect the designers to adhere to it at all - we encourage unique ideas. There is some sample text in the wireframe - this does not have to be used, but may provide ideas.

We provide an easy way for people to manage email for a custom domain name. For example if you own "yourhouseword.example" you can point your DNS records to us and we'll make it easy to have emails addressed to your domain get forwarded to your existing email (gmail, etc). Folks running blogs, and other small sites can quickly setup email addresses for their domains and manage them in one place.

(For technical folks, we have you point your dns mx records to us, hence the name. That way all your email hits us and we can redirect it wherever you want. We make it easy to manage a single domain or a bunch of domains. Many domain registrars offer this service for a fee, and have clumsy management tools. We provide a robust simple toolset for free, as well as premium options).

The goal of the landing page is to get folks into the signup flow. The second priority flow is to have them take a look at the premium plan offerings.

We may offer the winning designer additional work for the remainder of the site design.
Updates

I've changed this project to a committed payment.  It is no longer refundable.  Thank you.

Target Market(s)

Bloggers, podcasters, designers, app developers - people who are a little tech savvy.

Industry/Entity Type

It Company

Font styles to use
Sans Serif

Colors

Designer to choose colors to be used in the design.

Requirements
Must have
• A full fidelity mockup (comp) of the landing page including the source file (psd, ai, etc).

Some sort of logo treatment for the pingo.qz brand

A call to action for signup, such as the suggested 'Get Started Here'
Nice to have
• A hip startup feel

Incorporation of the email theme

Give the impression it is simple, easy and fast

```html
<!DOCTYPE html>
<html lang="en">
<head>
<meta charset="utf-8">
<title>Pingo.QZ — Email forwarding for your domain</title>
<link href="https://fonts.googleapis.com/css2?family=Arimo:wght@400;700&family=Oswald:wght@400&display=swap" rel="stylesheet">
<style>
:root{
  --blue:#1a8ad0;
  --yellow:#ffcc00;
  --white:#ffffff;
  --ink:#111111;
  --footer:#23272b;
  --strip:#e6e6e6;
  --strip-dark:#d2d2d2;
  --label:#7fc44a;
  --coral:#ef6d6d;
}
*{box-sizing:border-box;margin:0;padding:0}
html,body{width:1200px;height:752px;overflow:hidden;background:var(--white);font-family:Arimo,Arial,sans-serif}
.page{position:relative;width:1200px;height:752px}
.top-strip{position:absolute;left:0;top:0;width:1200px;height:10px;background:var(--strip)}
.top-strip span{position:absolute;top:0;height:10px;background:var(--strip-dark)}
.site-header{position:absolute;left:0;top:10px;width:1200px;height:81px;background:var(--white)}
.brand{position:absolute;left:199px;top:24px;font-family:Oswald,Arimo,sans-serif;font-size:33px;line-height:1;color:var(--blue)}
.main-nav a{position:absolute;top:0;height:81px;line-height:81px;font-size:12px;color:var(--ink);text-decoration:none}
.main-nav a.is-active{left:694px;width:56px;text-align:center;background:var(--blue);color:var(--white);border-bottom:4px solid var(--yellow);line-height:80px}
.hero{position:absolute;left:0;top:91px;width:1200px;height:430px;overflow:hidden}
.hero-bg{position:absolute;inset:0;background:
  radial-gradient(ellipse 520px 180px at 420px 0px,rgba(220,245,245,.95),rgba(220,245,245,0) 100%),
  radial-gradient(ellipse 300px 260px at 320px 320px,rgba(220,140,60,.75),rgba(220,140,60,0) 100%),
  radial-gradient(ellipse 300px 260px at 1000px 280px,rgba(190,140,70,.7),rgba(190,140,70,0) 100%),
  linear-gradient(180deg,#a8d8d4 0%,#8fb58e 30%,#a28b52 60%,#8a5a32 100%)}
.hero-shadow{position:absolute;left:200px;top:0;width:800px;height:8px;background:radial-gradient(ellipse at center top,rgba(0,0,0,.35),rgba(0,0,0,0) 70%)}
.hero-figure{position:absolute;left:630px;top:170px;width:190px;height:290px;border-radius:90px 90px 30px 30px;background:radial-gradient(ellipse at 50% 40%,#2f3440,#1b1e26 70%,rgba(27,30,38,0) 100%)}
.hero-title{position:absolute;left:199px;top:108px;font-size:30px;font-weight:400;color:var(--blue)}
.btn{position:absolute;left:199px;width:155px;text-align:center;font-size:16px;color:var(--white);text-decoration:none}
.btn-outline{top:167px;height:37px;line-height:33px;border:2px solid rgba(255,255,255,.75)}
.btn-primary{top:217px;height:34px;line-height:34px;background:var(--yellow)}
.steps{position:absolute;left:0;top:0}
.step-label{position:absolute;font-size:9px;color:var(--label);white-space:nowrap;transform:translateX(-50%)}
.carousel-dots{position:absolute;left:1086px;top:399px;display:flex;gap:6px}
.carousel-dots i{width:10px;height:10px;border-radius:50%;background:var(--white)}
.carousel-dots i.is-current{background:var(--blue)}
.guides{position:absolute;left:0;top:552px;width:1200px;height:85px}
.guide{position:absolute;top:0;width:341px;height:85px;background:var(--blue);color:var(--white)}
.guide h2{font-size:14px;font-weight:400;line-height:19px}
.guide p{margin-top:6px;font-size:10px;color:var(--ink)}
.guide-left{left:233px;padding:14px 20px 0 41px}
.guide-right{left:624px;padding:14px 28px 0 20px}
.guide-badge{position:absolute;top:-5px;z-index:2}
.site-footer{position:absolute;left:0;top:667px;width:1200px;height:85px;background:var(--footer);color:var(--white)}
.footer-nav{position:absolute;left:199px;top:27px;font-size:11px}
.footer-nav a{color:var(--white);text-decoration:none}
.copyright{position:absolute;left:200px;top:55px;font-size:11px}
.social{position:absolute;left:880px;top:30px;display:flex;gap:16px;font-size:13px;color:#8c9094}
</style>
</head>
<body>
<div class="page">
  <div class="top-strip">
    <span style="left:90px;width:74px"></span><span style="left:221px;width:34px"></span>
    <span style="left:366px;width:20px"></span><span style="left:617px;width:74px"></span>
    <span style="left:891px;width:21px"></span><span style="left:998px;width:58px"></span>
    <span style="left:1089px;width:74px"></span>
  </div>

  <header class="site-header">
    <div class="brand">Pingo.QZ</div>
    <nav class="main-nav">
      <a href="#" class="is-active">Home</a>
      <a href="#" style="left:769px">How It Works</a>
      <a href="#" style="left:866px">Support</a>
      <a href="#" style="left:936px">Login</a>
    </nav>
  </header>

  <section class="hero">
    <div class="hero-bg" role="img" aria-label="Blurred outdoor photo background in teal, green and amber tones"></div>
    <div class="hero-shadow"></div>
    <div class="hero-figure" role="img" aria-label="Photo of a businessman in a suit sitting cross-legged in meditation"></div>

    <h1 class="hero-title">Nulla molestie laoreet</h1>
    <a href="#" class="btn btn-outline">Get Started Here</a>
    <a href="#" class="btn btn-primary">Compare Plans</a>

    <svg class="steps" width="1200" height="430" viewBox="0 0 1200 430">
      <path d="M499 230 Q560 170 642 145 Q740 110 829 145 Q900 170 953 214" fill="none" stroke="rgba(255,255,255,.6)" stroke-width="1"/>
      <g fill="#fff" stroke="#e4e4e4" stroke-width="2">
        <circle cx="499" cy="230" r="29"/><circle cx="642" cy="145" r="29"/>
        <circle cx="829" cy="145" r="29"/><circle cx="953" cy="214" r="29"/>
      </g>
      <g>
        <rect x="484" y="220" width="30" height="20" fill="#f6a623"/>
        <path d="M484 220 L499 232 L514 220" fill="none" stroke="#c0601a" stroke-width="1.5"/>
        <path d="M628 145 L642 131 L656 145 L642 159 Z" fill="#f6b81f"/>
        <rect x="818" y="131" width="22" height="27" rx="3" fill="#c9c9c9"/>
        <rect x="939" y="206" width="28" height="14" rx="7" fill="#b8b8b8"/>
      </g>
      <path d="M103 300 L96 311 L103 322" fill="none" stroke="var(--coral)" stroke-width="2.5"/>
      <path d="M1109 300 L1116 311 L1109 322" fill="none" stroke="var(--coral)" stroke-width="2.5"/>
    </svg>
    <span class="step-label" style="left:501px;top:272px">Consider Your Suitability</span>
    <span class="step-label" style="left:641px;top:187px">Consider Your Idea</span>
    <span class="step-label" style="left:833px;top:187px">Consider Your Market</span>
    <span class="step-label" style="left:956px;top:256px">Success Your Business</span>

    <div class="carousel-dots"><i class="is-current"></i><i></i><i></i><i></i></div>
  </section>

  <section class="guides">
    <article class="guide guide-left">
      <h2>How to configure your SkyRelay DNS to use pingo.qz</h2>
      <p>Lorem ipsum itit dolor. Lorem ipsum itit dolor.</p>
    </article>
    <article class="guide guide-right">
      <h2>Use pingo.qz with your NameHarbor domain registration for reliable email forwarding</h2>
      <p>Lorem ipsum itit dolor. Lorem ipsum itit dolor.</p>
    </article>
    <svg class="guide-badge" style="left:190px" width="80" height="95" viewBox="0 0 80 95">
      <circle cx="35" cy="46" r="34" fill="#fff"/>
      <circle cx="35" cy="46" r="23" fill="var(--yellow)"/>
      <path d="M24 52 h21 a6 6 0 0 0 0-12 a8 8 0 0 0-15-2 a6 6 0 0 0-6 14z" fill="#fff"/>
    </svg>
    <svg class="guide-badge" style="left:930px" width="80" height="95" viewBox="0 0 80 95">
      <circle cx="44" cy="46" r="34" fill="#fff"/>
      <circle cx="44" cy="46" r="23" fill="var(--yellow)"/>
      <circle cx="44" cy="46" r="9" fill="none" stroke="#fff" stroke-width="2"/>
    </svg>
  </section>

  <footer class="site-footer">
    <nav class="footer-nav">
      <a href="#">Home</a> &nbsp;/&nbsp; <a href="#">How It works</a> &nbsp;/&nbsp; <a href="#">Support</a> &nbsp;/&nbsp; <a href="#">Login</a>
    </nav>
    <div class="copyright">© 2014 Pingo.QZ</div>
    <div class="social"><span>Linkway</span><span>Chatter</span><span>Callbox</span></div>
  </footer>
</div>
</body>
</html>
```